Electrician Letterhead Design MVR

We need some letterhead for our bills and other papers.
Customer address is on the right side (Swiss format)
A4 format

Design should also be applicable on Cards

Target Market(s)

Private Customers, Small Business

Industry/Entity Type

Electrician

Other font styles liked:
• incised 901

Colors
00AB8E
00BBA5
67D7C9
C6EFE9
E9F9F6

```html
<!DOCTYPE html>
<html lang="en">
<head>
<meta charset="utf-8">
<title>MVR Stationery</title>
<link href="https://fonts.googleapis.com/css2?family=Lato:ital,wght@0,400;0,700;0,900&family=Dancing+Script:wght@500&display=swap" rel="stylesheet">
<style>
:root{
  --brand:#00A28F;
  --brand-dark:#00937F;
  --paper:#E6E6E6;
  --paper-light:#EDEDED;
  --backdrop:#F2F2F2;
  --ink:#3A3A3A;
  --window:#B5B5B5;
  --white:#FFFFFF;
}
*{margin:0;padding:0;box-sizing:border-box}
html,body{width:1200px;height:889px;overflow:hidden}
body{background:var(--backdrop);font-family:'Lato',sans-serif;color:var(--ink);position:relative}
.sheet{position:absolute;background:var(--paper);box-shadow:0 2px 6px rgba(0,0,0,.12)}
.brand-mark{position:absolute;font-family:'Lato',sans-serif;font-weight:900;color:var(--brand);line-height:1;display:flex;align-items:center;gap:.12em;letter-spacing:.02em}
.brand-mark .dot{display:inline-block;width:.28em;height:.28em;background:currentColor}
.brand-mark.on-brand{color:var(--white)}

/* letterhead */
.letterhead{left:242px;top:110px;width:329px;height:468px}
.letterhead .brand-mark{left:25px;top:20px;font-size:30px}
.contact{position:absolute;border-left:.6px solid var(--brand);padding-left:4px;font-size:5.3px;line-height:1.5}
.contact .row{display:flex;align-items:center;gap:3px}
.contact .icon{width:4px;height:4px;fill:var(--brand);flex:none}
.letterhead .contact{left:224px;top:21px;height:36px}
.letter-body{position:absolute;left:27px;top:102px;width:278px;font-size:6.1px;line-height:1.17}
.letter-body p{margin-bottom:7.4px;text-align:justify}
.letter-body .date{margin-bottom:8px}
.letter-body .salutation{font-weight:700;font-size:7.6px;margin-bottom:8px}
.letter-body .regards{margin-top:14px}
.signature{font-family:'Dancing Script',cursive;font-size:14px;margin-top:8px;color:#333}

/* folder */
.folder{left:628px;top:88px;width:388px;height:490px;background:var(--brand)}
.folder .brand-mark{right:47px;top:392px;font-size:54px}

/* cards */
.card-front{left:123px;top:615px;width:151px;height:86px;background:var(--paper-light)}
.card-front .brand-mark{left:10px;top:34px;font-size:19px}
.card-front .contact{left:78px;top:20px;height:60px;font-size:4px}
.card-front .name{color:var(--brand);font-weight:700;font-size:4.6px}
.card-front .role{margin-bottom:3px}
.card-front .contact .icon{width:3px;height:3px}
.card-back{left:123px;top:722px;width:151px;height:87px;background:var(--brand)}
.card-back .brand-mark{left:0;right:0;top:26px;justify-content:center;font-size:32px}

/* envelopes */
.envelope-front{left:312px;top:626px;width:369px;height:178px;background:var(--paper-light)}
.envelope-front .brand-mark{left:15px;top:16px;font-size:24px}
.envelope-front .contact{left:15px;top:115px;border-left:none;padding-left:0;font-size:5.6px;line-height:1.55}
.envelope-front .address-window{position:absolute;left:244px;top:106px;width:94px;height:37px;background:var(--window);border:.8px solid var(--brand)}
.envelope-back{left:712px;top:626px;width:372px;height:178px;background:var(--paper-light)}
.envelope-back svg{position:absolute;left:0;top:0}
</style>
</head>
<body>

<svg width="0" height="0" style="position:absolute">
  <defs>
    <symbol id="ico-phone" viewBox="0 0 10 10"><path d="M2 1h2l1 2.5-1.3 1a5 5 0 0 0 2.8 2.8l1-1.3L10 7v2c0 .6-.4 1-1 1A9 9 0 0 1 0 1c0-.6.4-1 1-1z"/></symbol>
    <symbol id="ico-mail" viewBox="0 0 10 10"><path d="M0 2h10v6H0z M0 2l5 3.5L10 2" /></symbol>
    <symbol id="ico-web" viewBox="0 0 10 10"><circle cx="5" cy="5" r="5"/></symbol>
  </defs>
</svg>

<section class="sheet letterhead">
  <div class="brand-mark">MVR<span class="dot"></span></div>
  <div class="contact">
    <div>42 Lindenweg 7,</div>
    <div>3011 Bern</div>
    <div class="row"><svg class="icon"><use href="#ico-phone"/></svg>031-555-0142</div>
    <div class="row"><svg class="icon"><use href="#ico-mail"/></svg>hello@mvr-elektro.ch</div>
    <div class="row"><svg class="icon"><use href="#ico-web"/></svg>www.mvr-elektro.ch</div>
  </div>
  <div class="letter-body">
    <p class="date">Feb-03-2022</p>
    <p>Ms, Anna Keller<br>President</p>
    <p>Nordlicht AG<br>18 Seeweg, Suite 4<br>Luzern, 6003</p>
    <p class="salutation">Dear Ms, Keller</p>
    <p>Lorem ipsum dolor sit amet, consectetur adipisicing elit, sed do eiusmod tempor incididunt ut labore et dolore magna aliqua. Ut enim ad minim veniam, quis nostrud exercitation ullamco laboris nisi ut aliquip ex ea commodo consequat. Duis aute irure dolor in reprehenderit in voluptate velit esse cillum dolore eu fugiat nulla pariatur.</p>
    <p>Lorem ipsum dolor sit amet, consectetur adipisicing elit, sed do eiusmod tempor incididunt ut labore et dolore magna aliqua. Ut enim ad minim veniam, quis nostrud exercitation ullamco laboris nisi ut aliquip ex ea commodo consequat. Duis aute irure dolor in reprehenderit in voluptate velit esse cillum dolore eu fugiat nulla pariatur.</p>
    <p>Lorem ipsum dolor sit amet, consectetur adipisicing elit, sed do eiusmod tempor incididunt ut labore et dolore magna aliqua. Ut enim ad minim veniam, quis nostrud exercitation ullamco laboris nisi ut aliquip ex ea commodo consequat.</p>
    <p>Excepteur sint occaecat cupidatat non proident, sunt in culpa qui officia deserunt mollit anim id est laborum. re et dolore magnam aliquam quaerat voluptatem.</p>
    <p class="regards">Regards</p>
    <div class="signature">Lukas Brandt</div>
  </div>
</section>

<section class="sheet folder">
  <div class="brand-mark on-brand">MVR<span class="dot"></span></div>
</section>

<section class="sheet card-front">
  <div class="brand-mark">MVR<span class="dot"></span></div>
  <div class="contact">
    <div class="name">PETRA IMHOF</div>
    <div class="role">Co-Founder</div>
    <div>42 Lindenweg 7,</div>
    <div>3011 Bern</div>
    <div class="row"><svg class="icon"><use href="#ico-phone"/></svg>031-555-0142</div>
    <div class="row"><svg class="icon"><use href="#ico-mail"/></svg>hello@mvr-elektro.ch</div>
    <div class="row"><svg class="icon"><use href="#ico-web"/></svg>www.mvr-elektro.ch</div>
  </div>
</section>

<section class="sheet card-back">
  <div class="brand-mark on-brand">MVR<span class="dot"></span></div>
</section>

<section class="sheet envelope-front">
  <div class="brand-mark">MVR<span class="dot"></span></div>
  <div class="contact">
    <div>42 Lindenweg 7,</div>
    <div>3011 Bern</div>
    <div class="row"><svg class="icon"><use href="#ico-phone"/></svg>031-555-0142</div>
    <div class="row"><svg class="icon"><use href="#ico-mail"/></svg>hello@mvr-elektro.ch</div>
    <div class="row"><svg class="icon"><use href="#ico-web"/></svg>www.mvr-elektro.ch</div>
  </div>
  <div class="address-window"></div>
</section>

<section class="sheet envelope-back">
  <svg width="372" height="60" viewBox="0 0 372 60">
    <path d="M1 0H371L359 44Q356 53 346 53H26Q16 53 13 44Z" fill="var(--brand)"/>
  </svg>
</section>

</body>
</html>
```